Band and Coaching business card (creative industry)

My company The Fenwick Ensemble is the name of my band Soul outfit but is also a brand I use for my coaching business which is Performance coaching in the following areas: Corporate coaching, acting, vocals and dialect. The band plays for corporate events and private functions as well as local bar/restaurant/festivals.
Updates

Hi All

Please see updated info for the wording of the business card front and back.  This is ito then be followed with contact number, email and facebook link

first side should have:

JulieRose Brannigan
Creative Director
( followed by contact info as per previous)

Side 2:

The Fenwick Ensemble  - Band  
 Vocalist      I   Musician    I  Songwriter

The Fenwick Ensemble  - Studio
Performance Coaching  
Acting  I  Vocals  I Dialect  I Corporate Coaching

Industry/Entity Type

Events

Contact Information for Business Card

The Fenwick Ensemble (logo)
JulieRose Brannigan
Musician/Vocalist/Performance Coach
M: 0412 605 918
E: thefenwickensemble@mailbrook.net
W: www.friendspace.net/thefenwickensembleband

Font styles to use
Sans Serif

Requirements
Must have
• first side should have:

JulieRose Brannigan
Creative Director

Side 2:

The Fenwick Ensemble - Band
Vocalist I Musician I Songwriter

The Fenwick Ensemble - Studio
Performance Coaching
Acting I Vocals I Dialect I Corporate Coaching
Nice to have
• I like smaller business cards with curved edges.

some ideas for look in additional business cards attached.
Should not have
• music notes or anything specific to the field. Want to keep it funky and contemporary

```html
<!DOCTYPE html>
<html lang="en">
<head>
<meta charset="UTF-8">
<title>The Fenwick Ensemble – Business Card</title>
<link href="https://fonts.googleapis.com/css2?family=Lato:wght@400;700&display=swap" rel="stylesheet">
<style>
  :root {
    --magenta: #e61ec6;
    --emblem: #b41fe6;
    --paper: #ffffff;
    --white: #ffffff;
  }
  html, body {
    margin: 0;
    padding: 0;
    overflow: hidden;
    background: var(--paper);
  }
  .card {
    position: relative;
    width: 1200px;
    height: 741px;
    background: var(--paper);
    font-family: "Lato", sans-serif;
    color: var(--magenta);
    overflow: hidden;
  }
  .emblem {
    position: absolute;
    left: 414px;
    top: 199px;
    width: 374px;
    height: 374px;
  }
  .emblem-name {
    position: absolute;
    left: 414px;
    top: 199px;
    width: 374px;
    height: 374px;
    display: flex;
    align-items: center;
    justify-content: center;
    text-align: center;
    color: var(--white);
    font-weight: 700;
    font-size: 50px;
    line-height: 1.1;
    margin: 0;
  }
  .division {
    position: absolute;
    margin: 0;
  }
  .division--band { left: 52px; top: 344px; }
  .division--studio { left: 828px; top: 344px; }
  .division-title {
    margin: 0;
    font-weight: 700;
    font-size: 24px;
    line-height: 34px;
    white-space: pre;
  }
  .division-subtitle {
    margin: 0;
    font-weight: 700;
    font-size: 19px;
    line-height: 26px;
  }
  .division-roles {
    margin: 0;
    font-weight: 400;
    font-size: 18px;
    line-height: 26px;
    white-space: pre;
  }
</style>
</head>
<body>
  <main class="card">
    <svg class="emblem" viewBox="0 0 374 374" aria-hidden="true">
      <circle cx="187" cy="187" r="187" fill="var(--emblem)"/>
    </svg>
    <p class="emblem-name">The<br>Fenwick<br>Ensemble</p>

    <section class="division division--band">
      <h2 class="division-title">The Fenwick Ensemble  - Band</h2>
      <p class="division-roles">Vocalist  I  Musician  I  Songwriter</p>
    </section>

    <section class="division division--studio">
      <h2 class="division-title">The Fenwick Ensemble  - Studio</h2>
      <p class="division-subtitle">Performance Coaching</p>
      <p class="division-roles">Acting I Vocals I Dialect I Corporate</p>
    </section>
  </main>
</body>
</html>
```